Business card for medical clinic

I need an upmarket, modern medical/health business card for my clinic

Contact Information for Business Card

name, address, email, qr code

```html
<!DOCTYPE html>
<html lang="en">
<head>
<meta charset="utf-8">
<title>Meridale Health Partners – Business Card</title>
<link rel="stylesheet" href="https://fonts.googleapis.com/css2?family=Montserrat:wght@400;500;800&display=swap">
<style>
  :root {
    --bg: #1b1b1d;
    --blue-light: #27aae2;
    --blue-mid: #1a77ae;
    --blue-deep: #17659a;
    --navy: #233d63;
    --ink: #1a1a1a;
    --band: #151515;
    --paper: #ffffff;
  }
  * { box-sizing: border-box; margin: 0; padding: 0; }
  html, body { width: 1200px; height: 880px; overflow: hidden; }
  body {
    background: var(--bg);
    font-family: "Montserrat", sans-serif;
    position: relative;
  }
  .card {
    position: absolute;
    width: 560px;
    height: 320px;
    border-radius: 26px;
    overflow: hidden;
    box-shadow: 0 18px 40px rgba(0,0,0,.55);
  }
  /* Front */
  .card--front {
    left: 60px; top: 100px;
    background: linear-gradient(160deg, var(--blue-light) 0%, var(--blue-light) 30%, var(--blue-mid) 62%, var(--blue-deep) 82%, var(--navy) 100%);
    display: flex; align-items: center; justify-content: center;
  }
  .brand {
    display: flex; align-items: center; gap: 18px;
    font-weight: 500; letter-spacing: .08em; text-transform: uppercase;
  }
  .brand__dot {
    width: 64px; height: 64px; border-radius: 50%;
    border: 5px solid currentColor; flex: none;
  }
  .brand__name { line-height: 1.15; }
  .card--front .brand { color: var(--paper); font-size: 30px; }
  /* Back */
  .card--back { left: 580px; top: 460px; background: var(--paper); }
  .card__band { position: absolute; inset: 0; width: 100%; height: 100%; }
  .card--back .brand {
    position: absolute; left: 40px; top: 96px;
    color: var(--blue-mid); font-size: 20px; gap: 12px;
  }
  .card--back .brand__dot { width: 42px; height: 42px; border-width: 4px; }
  .person {
    position: absolute; right: 44px; top: 26px; text-align: right;
  }
  .person__name { font-weight: 800; font-size: 22px; color: var(--blue-mid); letter-spacing: .01em; }
  .person__role { font-size: 14px; color: var(--ink); margin-top: 2px; }
  .accent-tab {
    position: absolute; right: 0; top: 22px; width: 18px; height: 40px;
    background: linear-gradient(180deg, var(--blue-mid), var(--blue-light));
  }
  .address {
    position: absolute; left: 40px; top: 160px;
    font-size: 14px; line-height: 1.4; color: var(--ink);
  }
  .contacts {
    position: absolute; left: 40px; top: 240px; list-style: none;
    font-size: 13.5px; color: var(--paper); line-height: 1.45;
  }
  .contacts li { display: flex; align-items: center; gap: 10px; }
  .contacts svg { width: 14px; height: 14px; fill: var(--blue-light); flex: none; }
  .ring {
    position: absolute; right: 26px; top: 128px;
    width: 96px; height: 96px; border-radius: 50%;
    border: 5px solid var(--blue-light);
    background: var(--paper);
  }
</style>
</head>
<body>
  <section class="card card--front" aria-label="Card front">
    <div class="brand">
      <span class="brand__dot"></span>
      <span class="brand__name">Meridale Health<br>Partners</span>
    </div>
  </section>

  <section class="card card--back" aria-label="Card back">
    <svg class="card__band" viewBox="0 0 560 320" preserveAspectRatio="none" aria-hidden="true">
      <polygon points="0,232 560,112 560,320 0,320" fill="var(--band)"/>
    </svg>
    <span class="accent-tab"></span>
    <div class="person">
      <p class="person__name">DANIEL HART</p>
      <p class="person__role">Managing Director</p>
    </div>
    <div class="brand">
      <span class="brand__dot"></span>
      <span class="brand__name">Meridale Health<br>Partners</span>
    </div>
    <p class="address">Your address, City<br>State, Zip 1234</p>
    <ul class="contacts">
      <li><svg viewBox="0 0 24 24"><path d="M6.6 10.8a15 15 0 0 0 6.6 6.6l2.2-2.2a1 1 0 0 1 1-.25 11.4 11.4 0 0 0 3.6.57 1 1 0 0 1 1 1V20a1 1 0 0 1-1 1A17 17 0 0 1 3 4a1 1 0 0 1 1-1h3.5a1 1 0 0 1 1 1c0 1.25.2 2.450.57 3.57a1 1 0 0 1-.25 1z"/></svg>123 456 789</li>
      <li><svg viewBox="0 0 24 24"><path d="M2 5h20v14H2zm2 2v.5l8 5 8-5V7l-8 5z"/></svg>info@meridalehealth.com</li>
      <li><svg viewBox="0 0 24 24"><circle cx="12" cy="12" r="10"/></svg>www.meridalehealth.com</li>
    </ul>
    <span class="ring"></span>
  </section>
</body>
</html>
```